Tamsorellium we are a young innovative brand about making life easier for people with a disability

Our tag line is Making Life Easy, we are still a relatively new company trying to bring innovation and excitement into the disability space - with latest products and technology - we do have existing website but need to unpgrade for a stronger visual presence.

```html
<!DOCTYPE html>
<html lang="en">
<head>
<meta charset="utf-8">
<title>Tamsorellium — Making Life Easy</title>
<link href="https://fonts.googleapis.com/css2?family=Montserrat:ital,wght@0,400;0,500;0,600;0,700;0,800;1,500;1,800&display=swap" rel="stylesheet">
<style>
:root{
  --red:#e0141b;
  --navy:#15233a;
  --blue:#1d5a91;
  --blue-deep:#174b7c;
  --grey-band:#f2f3f6;
  --soft:#eef1f5;
  --text:#4a4f5a;
  --muted:#8a8f99;
  --line:#d6d9df;
  --white:#ffffff;
}
*{box-sizing:border-box;margin:0;padding:0}
html,body{width:1200px;height:4124px;overflow:hidden}
body{font-family:"Montserrat",sans-serif;color:var(--text);background:var(--white);position:relative}
.abs{position:absolute}
.photo{position:absolute}
a{color:inherit;text-decoration:none}

/* hero */
.hero{position:absolute;left:0;top:0;width:1200px;height:632px}
.hero-photo{left:0;top:0;width:1200px;height:632px;background:linear-gradient(100deg,#3c3f3c 0%,#6b6a5d 35%,#8c8a78 55%,#5f6a5a 80%,#3f4a40 100%)}
.hero-shade{left:0;top:0;width:1200px;height:632px;background:linear-gradient(90deg,rgba(0,0,0,.45),rgba(0,0,0,.05) 70%)}
.topbar{top:16px;left:176px;width:880px;height:22px;color:#fff;font-size:13px;display:flex;align-items:center}
.topbar .item{display:flex;align-items:center;gap:9px;margin-right:28px}
.topbar .social{margin-left:auto;display:flex;gap:16px}
.topbar .social span{width:20px;height:20px;border:2px solid #fff;border-radius:50%}
.nav{left:133px;top:58px;width:934px;height:70px;background:rgba(255,255,255,.95);display:flex;align-items:center;padding:0 42px 0 42px}
.brand{display:flex;align-items:center;gap:8px;font-weight:800;font-size:17px;color:var(--red);letter-spacing:.3px}
.brand .dot{width:30px;height:30px;border-radius:50%;background:var(--red)}
.nav ul{list-style:none;display:flex;gap:34px;margin-left:auto;font-size:14px;font-weight:600;color:var(--navy);letter-spacing:.6px}
.hero h1{left:176px;top:292px;font-size:45px;font-weight:800;color:#fff;letter-spacing:4px}
.hero p{left:176px;top:354px;width:400px;color:#fff;font-size:13.5px;line-height:21px;font-weight:500}
.btn-red{background:var(--red);color:#fff;font-weight:700;display:flex;align-items:center;justify-content:center;gap:10px}
.hero .btn-red{left:176px;top:416px;width:253px;height:40px;font-size:14px}

/* about */
.about-photo{left:90px;top:774px;width:532px;height:397px;background:linear-gradient(135deg,#3b4437,#6d7a52 45%,#a8ad96 70%,#4b5840)}
.vline{left:657px;top:824px;width:2px;height:344px;background:var(--line)}
.dotline{border-left:2px dotted var(--line);width:0}
.eyebrow{font-size:12px;font-weight:800;font-style:italic;letter-spacing:1.6px;color:var(--blue);text-transform:uppercase}
.h2{font-size:36px;font-weight:600;color:var(--navy);letter-spacing:1.2px;line-height:41px}
.about .eyebrow{left:691px;top:797px}
.about .h2{left:691px;top:821px;width:400px}
.about p{left:691px;top:961px;width:332px;font-size:13.3px;line-height:18.5px;letter-spacing:1px;text-align:justify}
.btn-outline{border:2px solid var(--red);color:var(--red);font-weight:700;font-size:13.5px;letter-spacing:.8px;display:flex;align-items:center;justify-content:center;gap:8px;background:#fff}
.about .btn-outline{left:690px;top:1098px;width:131px;height:36px}

/* offer */
.offer-band{left:0;top:1504px;width:1200px;height:528px;background:var(--grey-band)}
.offer-title{left:300px;top:1344px;width:324px;text-align:right}
.offer-lede{left:691px;top:1350px;width:333px;font-size:13.3px;line-height:18.5px;letter-spacing:1px;text-align:justify}
.card{position:absolute;top:1435px;width:275px;height:431px;background:#fff;box-shadow:0 4px 12px rgba(20,30,50,.08)}
.card .img{height:272px}
.card h3{margin:20px 0 0 22px;font-size:17px;font-weight:700;color:var(--red);letter-spacing:1.8px}
.card p{margin:14px 22px 0;font-size:13px;line-height:18.5px;letter-spacing:1.1px}
.card svg{position:absolute;left:22px;top:397px}
.offer-btn{left:499px;top:1914px;width:202px;height:36px}

/* reviews */
.reviews{left:0;top:2032px;width:1200px;height:466px;background:linear-gradient(90deg,var(--blue-deep),var(--blue) 50%,var(--blue-deep))}
.reviews .eyebrow{left:0;top:46px;width:1200px;text-align:center;color:#fff}
.reviews .h2{left:0;top:60px;width:1200px;text-align:center;color:#fff}
.testimonial{left:501px;top:204px;width:450px;display:flex;flex-direction:column;gap:16px;color:#fff}
.quote{font-style:italic;font-weight:500;font-size:14px;line-height:18.7px;letter-spacing:.4px}
.quote-by{font-size:16px;letter-spacing:1px}

/* blog */
.blog-eyebrow{left:0;top:2581px;width:1200px;text-align:center}
.blog-title{left:0;top:2596px;width:1200px;text-align:center}
.post-big{left:176px;top:2666px;width:522px;height:283px;background:linear-gradient(120deg,#8e8f8c,#b9b6ad 40%,#6f6e69 75%,#9c9b94)}
.post h4{font-size:13.5px;font-weight:700;color:var(--navy)}
.post .date{font-size:10px;color:var(--muted);margin-top:4px}
.post p{font-size:13.3px;line-height:21px;color:var(--text);margin-top:4px}
.read{left:176px;top:3089px;font-size:13px;font-weight:700;color:var(--navy);text-decoration:underline}
.blog-btn{left:176px;top:3139px;width:181px;height:37px;font-weight:600}

/* contact */
.contact{left:0;top:3254px;width:1200px;height:448px;background:var(--soft)}
.contact-photo{left:0;top:0;width:420px;height:448px;background:linear-gradient(90deg,rgba(180,188,200,.55),rgba(238,241,245,0))}
.contact .eyebrow{left:176px;top:52px}
.contact .h2{left:176px;top:74px;width:320px}
.contact .intro{left:176px;top:168px;width:310px;font-size:13.3px;line-height:21px}
.field-label{position:absolute;left:534px;font-size:13px;color:var(--navy)}
.field{position:absolute;left:608px;width:416px;height:34px;background:#fff;border:1px solid var(--line);font-size:12.5px;color:#b4b8c0;padding:9px 14px}
.send{left:608px;top:317px;width:179px;height:35px;font-size:14px}

/* footer */
.footer{left:0;top:3702px;width:1200px;height:422px;background:var(--blue);color:#fff}
.footer .brand{position:absolute;left:176px;top:106px;color:#fff}
.footer .brand .dot{background:var(--red)}
.footer .about-text{left:178px;top:158px;width:190px;font-size:13.3px;line-height:21px}
.col{position:absolute;top:108px}
.col h5{font-size:12px;font-weight:600;letter-spacing:1.6px;color:rgba(255,255,255,.55);text-transform:uppercase;margin-bottom:12px}
.col li{list-style:none;font-size:13.5px;letter-spacing:.8px;line-height:26px;display:flex;align-items:flex-start;gap:10px}
.col li .ic{width:14px;height:14px;border:1.6px solid #fff;border-radius:50%;margin-top:6px;flex:none}
.col li .sq{border-radius:3px}
.footer .rule{left:176px;top:375px;width:848px;height:1px;background:rgba(255,255,255,.3)}
.copy{left:0;top:392px;width:1200px;text-align:center;font-size:12px;color:rgba(255,255,255,.55)}
</style>
</head>
<body>

<header class="hero">
  <div class="photo hero-photo" role="img" aria-label="Photo of friends, one in a wheelchair, laughing together at an outdoor picnic table"></div>
  <div class="photo hero-shade"></div>
  <div class="abs topbar">
    <span class="item">
      <svg width="17" height="17" viewBox="0 0 17 17"><circle cx="8.5" cy="8.5" r="8.5" fill="#fff"/><path d="M5.5 4.5l2 2-1 1c.6 1.3 1.7 2.4 3 3l1-1 2 2-1.2 1.2C8.7 12.4 4.6 8.3 4.3 5.7z" fill="#333"/></svg>
      269-5550184</span>
    <span class="item">
      <svg width="18" height="18" viewBox="0 0 18 18"><circle cx="9" cy="9" r="9" fill="#fff"/><rect x="4.5" y="6" width="9" height="6.5" fill="none" stroke="#333" stroke-width="1.3"/><path d="M4.5 6l4.5 3.6L13.5 6" fill="none" stroke="#333" stroke-width="1.3"/></svg>
      hello@tamsorellium.com.au</span>
    <span class="social"><span></span><span></span><span></span></span>
  </div>
  <nav class="abs nav">
    <a class="brand" href="#"><span class="dot"></span>TAMSORELLIUM</a>
    <ul><li>About Us</li><li>Products</li><li>Services</li><li>Blog</li><li>Contact Us</li></ul>
  </nav>
  <h1 class="abs">MAKING LIFE EASY</h1>
  <p class="abs">Bringing innovation and excitement to the disability space with cutting edge technology.</p>
  <a class="abs btn-red" href="#">Find Out How
    <svg width="18" height="16" viewBox="0 0 18 16"><path d="M2 14c1-5 4-7 9-7V3l5 5-5 5V9.5c-4 0-6.5 1.3-9 4.5z" fill="none" stroke="#fff" stroke-width="1.6" stroke-linejoin="round"/></svg>
  </a>
</header>

<section class="about">
  <div class="photo about-photo" role="img" aria-label="Photo of a man in a wheelchair talking with a friend beside an accessible vehicle ramp"></div>
  <div class="abs vline"></div>
  <div class="abs dotline" style="left:657px;top:1180px;height:210px"></div>
  <div class="abs eyebrow">Who We Are</div>
  <h2 class="abs h2">We Are Leading Innovators In Assistive Tech</h2>
  <p class="abs">Lorem ipsum dolor sit amet, consectetur adipiscing elit, sed do eiusmod tempor incididunt ut labore et dolore magna aliqua. Quis ipsum suspendisse ultrices gravida. Risus commodo viverra maecenas accumsan lacus vel facilisis.</p>
  <a class="abs btn-outline" href="#">Learn More</a>
</section>

<section class="offer">
  <div class="abs offer-band"></div>
  <h2 class="abs h2 offer-title">What We Offer</h2>
  <p class="abs offer-lede">Lorem ipsum dolor sit amet, consectetur adipiscing elit, sed do eiusmod tempor</p>
  <article class="card" style="left:176px">
    <div class="img" role="img" aria-label="Photo of a woman in a wheelchair working at a laptop" style="background:linear-gradient(135deg,#e9e6e0,#b9b2a6 55%,#7c2a2e)"></div>
    <h3>WHEELCHAIRS</h3>
    <p>Browse our extensive list of innovative gear designed to make movement fun.</p>
    <svg width="24" height="12" viewBox="0 0 24 12"><path d="M0 6h22M17 1l5 5-5 5" fill="none" stroke="#e0141b" stroke-width="1.6"/></svg>
  </article>
  <article class="card" style="left:464px">
    <div class="img" role="img" aria-label="Photo of a powered mobility chair close up" style="background:linear-gradient(135deg,#4a4a48,#1f1f20 55%,#5b5b58)"></div>
    <h3>MOBILITY UNITS</h3>
    <p>Browse our extensive list of innovative gear designed to make movement fun.</p>
    <svg width="24" height="12" viewBox="0 0 24 12"><path d="M0 6h22M17 1l5 5-5 5" fill="none" stroke="#e0141b" stroke-width="1.6"/></svg>
  </article>
  <article class="card" style="left:752px">
    <div class="img" role="img" aria-label="Photo of a wheelchair athlete playing a court sport" style="background:linear-gradient(135deg,#4c3a3a,#8a4c3e 45%,#2b2a2e)"></div>
    <h3>SPORTS EQUIPMENT</h3>
    <p>Browse our extensive list of innovative gear designed to make movement fun.</p>
    <svg width="24" height="12" viewBox="0 0 24 12"><path d="M0 6h22M17 1l5 5-5 5" fill="none" stroke="#e0141b" stroke-width="1.6"/></svg>
  </article>
  <a class="abs btn-outline offer-btn" href="#">Browse All Products</a>
</section>

<section class="abs reviews" role="region" aria-label="Customer reviews">
  <div class="abs eyebrow">Reviews</div>
  <h2 class="abs h2">What Our Customers Say</h2>
  <svg class="abs" style="left:220px;top:130px" width="250" height="240" viewBox="0 0 250 240">
    <polygon points="112,8 220,116 112,224 4,116" fill="#e0141b"/>
    <polygon points="125,18 224,116 125,214 26,116" fill="#c3c7cc"/>
  </svg>
  <div class="abs" role="img" aria-label="Photo of two men shaking hands, one seated in a wheelchair" style="left:246px;top:148px;width:200px;height:200px;transform:rotate(45deg) scale(.7);background:linear-gradient(135deg,#e8e4db,#9a8f7a)"></div>
  <svg class="abs" style="left:176px;top:236px" width="20" height="32" viewBox="0 0 20 32"><path d="M16 3L4 16l12 13" fill="none" stroke="rgba(255,255,255,.45)" stroke-width="3"/></svg>
  <svg class="abs" style="left:1004px;top:236px" width="20" height="32" viewBox="0 0 20 32"><path d="M4 3l12 13L4 29" fill="none" stroke="#fff" stroke-width="3"/></svg>
  <div class="abs testimonial">
    <p class="quote">Quis ipsum suspendisse ultrices gravida. Risus com modo viverra maecenas accumsan lacus vel facilisis. Lorem ipsum dolor sit amet, consectetur adipiscing elit, sed do eiusmod tempor incididunt umagna aliqua.</p>
    <div class="quote-by">- Marcus Delaney</div>
  </div>
  <svg class="abs" style="left:528px;top:406px" width="144" height="24" viewBox="0 0 144 24">
    <g fill="rgba(255,255,255,.4)"><rect x="4" y="5" width="13" height="13" transform="rotate(45 10.5 11.5)"/><rect x="33" y="5" width="13" height="13" transform="rotate(45 39.5 11.5)"/><rect x="91" y="5" width="13" height="13" transform="rotate(45 97.5 11.5)"/><rect x="121" y="5" width="13" height="13" transform="rotate(45 127.5 11.5)"/></g>
    <rect x="62" y="5" width="13" height="13" transform="rotate(45 68.5 11.5)" fill="#e0141b"/>
  </svg>
</section>

<section class="blog">
  <div class="abs eyebrow blog-eyebrow">Blog</div>
  <h2 class="abs h2 blog-title">Latest Articles</h2>
  <div class="photo post-big" role="img" aria-label="Photo of friends, two in wheelchairs, greeting each other at an outdoor café"></div>
  <div class="abs post" style="left:176px;top:2970px;width:522px">
    <h4>New Product Launch</h4>
    <div class="date">14 Oct 2023</div>
    <p>Ipsum dolor sit amet, consectetur adipiscing elit, sed do eiusmod tempor incididunt ut labore et dolore magna aliqua. Quis ipsum suspendisse ultrices gravida. Risus commodo viverra maecenas accumsan lacus vel</p>
  </div>
  <a class="abs read" href="#">Read More...</a>
  <a class="abs btn-outline blog-btn" href="#">Visit Blog
    <svg width="8" height="12" viewBox="0 0 8 12"><path d="M1.5 1.5L6 6l-4.5 4.5" fill="none" stroke="#e0141b" stroke-width="1.6"/></svg></a>
  <div class="abs dotline" style="left:709px;top:2666px;height:550px"></div>
  <div class="photo" role="img" aria-label="Photo of two friends chatting in a park, one in a wheelchair" style="left:722px;top:2666px;width:302px;height:116px;background:linear-gradient(120deg,#3f4b2e,#8a8f6a 50%,#d8d6cc)"></div>
  <div class="abs post" style="left:722px;top:2795px;width:302px">
    <h4>World Disability Awareness Day</h4>
    <div class="date">26 Aug 2023</div>
    <p>Ipsum dolor sit amet, consectetur adipiscing elit, sed do eiusmod tempor</p>
  </div>
  <div class="photo" role="img" aria-label="Photo of runners taking part in a marathon" style="left:724px;top:2904px;width:300px;height:115px;background:linear-gradient(120deg,#d9c45a,#c7703b 45%,#8fa9a0)"></div>
  <div class="abs post" style="left:724px;top:3034px;width:300px">
    <h4>Annual Marathon Event</h4>
    <div class="date">26 Aug 2023</div>
    <p>Ipsum dolor sit amet, consectetur adipiscing elit, sed do eiusmod tempor</p>
  </div>
</section>

<section class="abs contact">
  <div class="photo contact-photo" role="img" aria-label="Faded photo of a person seated in a wheelchair"></div>
  <div class="abs eyebrow">Contact</div>
  <h2 class="abs h2">Get In Touch With Us</h2>
  <p class="abs intro">Ipsum dolor sit amet, consectetur adipiscing elit, sed do eiusmod tempor incididunt ut labore et dolore magna aliqua. Quis ipsum suspendisse ultrices gravida.</p>
  <span class="field-label" style="top:54px">Name*</span><div class="field" style="top:45px">Name</div>
  <span class="field-label" style="top:107px">Email*</span><div class="field" style="top:98px">Email Address</div>
  <span class="field-label" style="top:160px">Phone*</span><div class="field" style="top:151px">Phone Number</div>
  <span class="field-label" style="top:210px">Message</span><div class="field" style="top:202px;height:98px">Type your message here</div>
  <a class="abs btn-red send" href="#">Send
    <svg width="8" height="12" viewBox="0 0 8 12"><path d="M1.5 1.5L6 6l-4.5 4.5" fill="none" stroke="#fff" stroke-width="1.8"/></svg></a>
</section>

<footer class="abs footer">
  <div class="brand"><span class="dot"></span>TAMSORELLIUM</div>
  <p class="abs about-text">Ipsum dolor sit amet, consectetur adipiscing elit, sed do eiusmod tempor incididunt ut labore et dolore magna aliqua.</p>
  <div class="col" style="left:446px">
    <h5>Quick Links</h5>
    <ul><li>About Us</li><li>Products</li><li>Services</li><li>Blog</li><li>Contact Us</li></ul>
  </div>
  <div class="col" style="left:637px">
    <h5>Social Media</h5>
    <ul><li><span class="ic sq"></span>Careers Network</li><li><span class="ic sq"></span>Short Posts</li><li><span class="ic sq"></span>Photo Feed</li></ul>
  </div>
  <div class="col" style="left:838px">
    <h5>Contact Info</h5>
    <ul>
      <li><span class="ic"></span>hello@tamsorellium.com.au</li>
      <li><span class="ic"></span>269-5550184</li>
      <li><span class="ic"></span>12 Orrin Lane<br>Belwood 3104<br>Canberra, NSW</li>
    </ul>
  </div>
  <div class="abs rule"></div>
  <div class="abs copy">© 2023 All Rights Reserved</div>
</footer>

</body>
</html>
```